Copper Lantern

Need a business card for our restaurant. Restaurant and Bar in the mountains of North Idaho. Rustic looking card

rustic design, wood and metal looking, primarily neutral colors

• Name, address, phone number, website, email address

```html
<!DOCTYPE html>
<html lang="en">
<head>
<meta charset="utf-8">
<title>Copper Lantern – Business Card</title>
<link rel="stylesheet" href="https://fonts.googleapis.com/css2?family=Cinzel:wght@400;600&family=Montserrat:wght@400;700&display=swap">
<style>
  :root {
    --bg-dark: #121212;
    --bg-mid: #2a2a2a;
    --card: #1c1c1c;
    --card-edge: #262626;
    --ink: #f2f2f2;
    --ink-soft: #cfcfcf;
    --shade: #2e2e2e;
  }
  * { margin: 0; padding: 0; box-sizing: border-box; }
  html, body { width: 1200px; height: 875px; overflow: hidden; }
  body {
    background: radial-gradient(ellipse at 40% 60%, var(--bg-mid), var(--bg-dark) 75%);
    font-family: "Montserrat", sans-serif;
    color: var(--ink);
    position: relative;
  }
  .card {
    position: absolute;
    width: 540px;
    height: 310px;
    background: linear-gradient(145deg, var(--card-edge), var(--card));
    border-radius: 18px;
    box-shadow: 0 24px 50px rgba(0,0,0,0.6);
    top: 282px;
  }
  .card--front { left: 45px; }
  .card--back { left: 615px; }

  .brand {
    display: flex;
    align-items: center;
    gap: 14px;
  }
  .brand__dot {
    width: 22px; height: 22px;
    border: 3px solid var(--ink);
    border-radius: 50%;
    flex: none;
  }
  .brand__name {
    font-family: "Cinzel", serif;
    font-weight: 600;
    color: var(--ink);
    letter-spacing: 0.12em;
    text-transform: uppercase;
  }
  .card--front .brand {
    position: absolute;
    left: 50%; top: 50%;
    transform: translate(-50%, -50%);
  }
  .card--front .brand__name { font-size: 30px; }
  .card--front .brand__dot { width: 30px; height: 30px; }

  .card--back .brand {
    position: absolute;
    left: 34px; top: 36px;
  }
  .card--back .brand__name { font-size: 17px; }

  .person {
    position: absolute;
    right: 34px; top: 34px;
    text-align: right;
  }
  .person__name { font-size: 20px; font-weight: 700; }
  .person__role { font-size: 12px; color: var(--ink-soft); margin-top: 2px; }

  .emblem-decor {
    position: absolute;
    right: 30px; top: 92px;
    width: 170px; height: 190px;
    border-radius: 12px;
    background: radial-gradient(ellipse at 55% 45%, var(--shade), transparent 70%);
  }

  .contact {
    position: absolute;
    left: 34px; bottom: 30px;
    font-size: 13px;
    line-height: 1.45;
    color: var(--ink);
  }
  .contact__address { margin-bottom: 10px; }
  .contact__list { list-style: none; }
  .contact__item { display: flex; align-items: center; gap: 9px; }
  .contact__icon { width: 13px; height: 13px; fill: var(--ink); flex: none; }
</style>
</head>
<body>
  <section class="card card--front" aria-label="Card front">
    <div class="brand">
      <span class="brand__dot"></span>
      <span class="brand__name">Copper Lantern</span>
    </div>
  </section>

  <section class="card card--back" aria-label="Card back">
    <div class="brand">
      <span class="brand__dot"></span>
      <span class="brand__name">Copper Lantern</span>
    </div>

    <div class="person">
      <div class="person__name">Daniel Reyes</div>
      <div class="person__role">Managing Director</div>
    </div>

    <div class="emblem-decor" role="img" aria-label="Faint embossed brand decoration"></div>

    <div class="contact">
      <p class="contact__address">48 Ridge Road,<br>Cedar Hollow, USA</p>
      <ul class="contact__list">
        <li class="contact__item">
          <svg class="contact__icon" viewBox="0 0 16 16" aria-hidden="true"><path d="M3 1h3l1.5 4-2 1.3a9 9 0 0 0 4.2 4.2L11 8.5l4 1.5v3a2 2 0 0 1-2 2A12 12 0 0 1 1 3a2 2 0 0 1 2-2z"/></svg>
          (08) 4410 2236
        </li>
        <li class="contact__item">
          <svg class="contact__icon" viewBox="0 0 16 16" aria-hidden="true"><path d="M1 3h14v10H1z M1 3l7 6 7-6" fill="none" stroke="#f2f2f2" stroke-width="1.6"/></svg>
          info@copperlantern.com
        </li>
        <li class="contact__item">
          <svg class="contact__icon" viewBox="0 0 16 16" aria-hidden="true"><circle cx="8" cy="8" r="6.5" fill="none" stroke="#f2f2f2" stroke-width="1.5"/><path d="M1.5 8h13M8 1.5c-3 3.5-3 9.5 0 13M8 1.5c3 3.5 3 9.5 0 13" fill="none" stroke="#f2f2f2" stroke-width="1.2"/></svg>
          www.copperlantern.com
        </li>
      </ul>
    </div>
  </section>
</body>
</html>
```